Business card design

I need my logo on this card, things I need the card to have on it
licensed and insured.
owner operators Milo & Trent Halvorsen
my phone number 5083716254
Disaster Recovery, Storm Damage Restoration, Proactive Disaster Plan Management, Roof Repair/Restoration Structural Repair and Reconstruction, Emergency Boarding and Tarping Service, Perimeter Fencing, Emergency Tree Removal,

```html
<!DOCTYPE html>
<html lang="en">
<head>
<meta charset="utf-8">
<title>Halvorsen's Construction – Business Card</title>
<link href="https://fonts.googleapis.com/css2?family=Nunito:wght@400;500;600&display=swap" rel="stylesheet">
<style>
  :root {
    --backdrop: #9b9b9b;
    --card-blue: #3d93d1;
    --brand-blue: #3a8fd0;
    --brand-faint: #6fb1e3;
    --ink: #1d1d1d;
    --white: #ffffff;
  }
  * { margin: 0; padding: 0; box-sizing: border-box; }
  html, body {
    width: 1093px; height: 1200px; overflow: hidden;
    background: var(--backdrop);
    font-family: "Nunito", sans-serif;
  }
  .card { position: absolute; border-radius: 18px; overflow: hidden; }
  .card--back { left: 265px; top: 224px; width: 580px; height: 362px; background: var(--card-blue); }
  .card--front { left: 262px; top: 620px; width: 585px; height: 359px; background: var(--white); }

  .brand-name {
    position: absolute; width: 220px; text-align: center;
    font-size: 21px; font-weight: 500; line-height: 1.3;
  }
  .card--back .brand-name { left: 40px; top: 152px; color: var(--brand-faint); }
  .card--front .brand-name { left: 40px; top: 152px; color: var(--brand-blue); }

  .divider { position: absolute; width: 1px; }
  .card--back .divider { left: 268px; top: 85px; height: 184px; background: rgba(255,255,255,0.6); }
  .card--front .divider { left: 285px; top: 90px; height: 212px; background: var(--brand-blue); }

  .services {
    position: absolute; left: 282px; top: 88px;
    list-style: none; color: var(--white);
    font-size: 14px; line-height: 25.2px;
  }
  .services li { position: relative; padding-left: 13px; }
  .services li::before {
    content: ""; position: absolute; left: 0; top: 9px;
    width: 7px; height: 7px; border-radius: 50%; background: var(--white);
  }
  .services li.wrap { line-height: 16px; padding-top: 4px; }

  .contact { position: absolute; left: 298px; top: 88px; color: var(--ink); }
  .contact__owners { font-size: 21px; font-weight: 500; color: var(--brand-blue); line-height: 1.2; }
  .contact__role { font-size: 13px; font-weight: 500; margin-top: 4px; }
  .contact__address { font-size: 13.5px; line-height: 16px; margin-top: 15px; }
  .contact__lines { list-style: none; margin-top: 12px; font-size: 13.5px; font-weight: 500; }
  .contact__lines li { display: flex; align-items: center; height: 23px; }
  .contact__lines svg { width: 14px; height: 14px; margin-right: 10px; fill: var(--brand-blue); }
  .contact__license { font-size: 13px; font-weight: 600; color: var(--brand-blue); margin-top: 8px; }
</style>
</head>
<body>

<section class="card card--back">
  <p class="brand-name">Halvorsen's Construction L.L.C</p>
  <div class="divider"></div>
  <ul class="services">
    <li>Disaster Recovery</li>
    <li>Storm Damage Restoration</li>
    <li>Proactive Disaster Plan Management</li>
    <li>Perimeter Fencing</li>
    <li>Emergency Boarding and Tarping Service</li>
    <li>Emergency Tree Removal</li>
    <li class="wrap">Roof Repair/Restoration Structural Repair<br>And Reconstruction</li>
  </ul>
</section>

<section class="card card--front">
  <p class="brand-name">Halvorsen's Construction L.L.C</p>
  <div class="divider"></div>
  <div class="contact">
    <p class="contact__owners">Milo &amp; Trent Halvorsen</p>
    <p class="contact__role">owner operators</p>
    <p class="contact__address">48 Cedar Hollow Lane<br>Brandon, MS 39047</p>
    <ul class="contact__lines">
      <li>
        <svg viewBox="0 0 16 16" aria-hidden="true"><path d="M1 6c0-2 3-3 7-3s7 1 7 3v1h-3V5.5C11 5 10 5 8 5s-3 0-4 .5V7H1z"/><path d="M4 8l1-2h6l1 2 1 5H3z"/><circle cx="8" cy="10" r="1.5" fill="#fff"/></svg>
        5083716254
      </li>
      <li>
        <svg viewBox="0 0 16 16" aria-hidden="true"><path d="M1 3h14v10H1z"/><path d="M1 3l7 6 7-6" fill="none" stroke="#fff" stroke-width="1.4"/></svg>
        info@halvorsenbuild.com
      </li>
      <li>
        <svg viewBox="0 0 16 16" aria-hidden="true"><circle cx="8" cy="8" r="7"/><path d="M3 6c2 0 3 1 3 3s-1 2 0 4M9 2c0 2 2 2 3 3s-1 3 1 4" fill="none" stroke="#fff" stroke-width="1.3"/></svg>
        www.halvorsenbuild.com
      </li>
    </ul>
    <p class="contact__license">Licensed and Insured</p>
  </div>
</section>

</body>
</html>
```